Luxury travel agency needs a website design

We are a travel agency specializing in booking luxury vacations. We specialize in Hawaii, Europe and Caribbean, but will do all vacations. I want a very classy website design which would attract luxury clients. The company name is "Harbors and Hammocks Travel Agency". Would love the web design to go with the color scheme of the logo. Hex codes included in files. Logo is attached. Would also love more Grey in the website. I want it very elegant

Coding

Coded - Design and coding required

Font styles to use
Sans Serif
Decorative

Requirements
Must have
• - Consultation Tab or a page where the client can fill out a short form about what vacation that they would want to book. I want this info to be sent to me in order for me to contact them.
- Somewhere with my contact info "email: marla@harborsandhammockstravel.example and phone number"
- Social media links
- About section "Marla Dunbevy - Agency Owner (picture provided)
Marla has been traveling full time for the passed two years and has been very passionate about travel from a young age. Marla is dedicated to working closely with clients to book their dream vacation.
Marla's specializations include honeymoons and anniversaries focusing on travel in Europe, Hawaii and all inclusive resorts in the Caribbean.

```html
<!DOCTYPE html>
<html lang="en">
<head>
<meta charset="utf-8">
<title>Harbors and Hammocks Travel Agency</title>
<link rel="stylesheet" href="https://fonts.googleapis.com/css2?family=Sancreek&family=Open+Sans:wght@400;600;700&display=swap">
<style>
:root{
  --yellow:#f0b84b;
  --orange:#e8603c;
  --ink:#1c1c1c;
  --dark:#1a1617;
  --grey:#e0dfe3;
  --text-grey:#777;
  --white:#fff;
}
*{margin:0;padding:0;box-sizing:border-box}
html,body{width:1200px;height:3542px;overflow:hidden}
body{position:relative;background:var(--white);font-family:"Open Sans",sans-serif;color:var(--ink)}
.abs{position:absolute}
.display{font-family:"Sancreek",serif;font-weight:400}
.btn{position:absolute;display:flex;align-items:center;justify-content:center;background:var(--yellow);color:var(--white);font-weight:700;font-size:17px;letter-spacing:1px;border-radius:40px;text-transform:uppercase}

/* header */
.top-line{left:0;top:0;width:1200px;height:4px;background:var(--yellow)}
.brand{left:145px;top:40px;display:flex;align-items:center;gap:10px;font-weight:700;font-size:22px;color:var(--ink)}
.brand .mark{width:22px;height:22px;border-radius:50%;background:var(--yellow)}
.header-email{left:650px;top:22px;display:flex;align-items:center;gap:10px;font-size:17px;font-weight:600}
.icon-circle{width:34px;height:34px;border-radius:50%;background:var(--orange);display:flex;align-items:center;justify-content:center}
.nav{left:549px;top:78px;display:flex;gap:43px;font-size:16px}
.nav a{color:var(--ink);text-decoration:none;padding-bottom:4px}
.nav a.active{color:var(--orange);border-bottom:3px solid var(--yellow)}

/* hero */
.hero{left:0;top:113px;width:1200px;height:667px;background:linear-gradient(180deg,#2d3f8a 0%,#4a4f9a 30%,#c8703a 52%,#2b3566 68%,#1b2550 100%)}
.hero-title{left:0;top:232px;width:1200px;text-align:center;font-size:60px;line-height:72px;color:var(--white)}
.hero-sub{left:0;top:408px;width:1200px;text-align:center;font-size:24px;line-height:33px;color:var(--white)}
.hero .dots{}
.dot{position:absolute;left:1120px;width:11px;height:11px;border-radius:50%;background:var(--white)}
.dot.on{background:var(--orange)}

/* about */
.about-title{left:146px;top:818px;font-size:46px;line-height:58px}
.about-text{left:146px;top:955px;width:400px;font-size:14.5px;line-height:24.8px;color:var(--text-grey)}
.portrait{left:640px;top:874px;width:364px;height:364px;border-radius:50%;background:radial-gradient(circle at 50% 40%,#b98a6e 0%,#6b4530 45%,#3aa9c4 100%)}

/* specialties */
.section-title{left:0;width:1200px;text-align:center;font-size:46px}
.card{top:1561px;width:295px;height:299px;border-radius:14px;overflow:hidden;display:flex;align-items:flex-end;justify-content:center;padding-bottom:48px;color:var(--white);font-weight:700;font-size:23px;letter-spacing:1px}
.card-hawaii{left:144px;background:linear-gradient(180deg,#4a5c8a,#c87b4a 55%,#2f6b6a)}
.card-europe{left:453px;background:linear-gradient(180deg,#3346a0,#6d86b4 50%,#5a9a3a 75%,#3f7a28)}
.card-caribbean{left:761px;background:linear-gradient(160deg,#294a5a,#17a0c0 50%,#0d4a82)}

/* gallery */
.photo{position:absolute}

/* footer */
.footer{left:0;top:3018px;width:1200px;height:524px;background:var(--dark)}
.footer-brand{left:0;top:3112px;width:1200px;display:flex;justify-content:center;align-items:center;gap:10px;color:var(--white);font-weight:700;font-size:26px}
.footer-brand .mark{width:24px;height:24px;border-radius:50%;background:var(--yellow)}
.footer-head{top:3195px;color:var(--white);font-size:17px}
.field{position:absolute;background:var(--white);border:1px solid #ccc;font-size:11px;color:#777;padding:8px 10px}
.submit{left:649px;top:3407px;width:78px;height:28px;font-size:12px;background:linear-gradient(180deg,#f5c35a,#c98d2a)}
.contact-item{left:782px;display:flex;align-items:center;gap:16px;color:var(--white);font-size:12.5px;line-height:17px}
.ring{width:34px;height:34px;border:1.5px solid var(--white);border-radius:50%;display:flex;align-items:center;justify-content:center;flex:none}
.copyright{left:183px;top:3484px;color:var(--white);font-size:12px}
.social{top:3482px;width:22px;height:22px;border-radius:50%;background:var(--white)}
</style>
</head>
<body>

<!-- header -->
<div class="abs top-line"></div>
<div class="abs brand"><span class="mark"></span>Harbors &amp; Hammocks</div>
<div class="abs header-email">
  <span class="icon-circle"><svg width="16" height="12" viewBox="0 0 16 12"><rect x="0.5" y="0.5" width="15" height="11" rx="1" fill="none" stroke="#fff"/><path d="M1 1 L8 7 L15 1" fill="none" stroke="#fff"/></svg></span>
  marla@harborsandhammockstravel.example
</div>
<nav class="abs nav">
  <a class="active" href="#">HOME</a><a href="#">CONSULTATION</a><a href="#">FORM</a><a href="#">ABOUT</a><a href="#">CONTACT</a>
</nav>

<!-- hero -->
<div class="abs hero" role="img" aria-label="Tropical beach at sunset with palm trees and rocky shoreline"></div>
<h1 class="abs hero-title display">Harbors &amp; Hammocks<br>Travel Agency</h1>
<p class="abs hero-sub">We are a travel agency specializing<br>in booking luxury vacations</p>
<div class="btn" style="left:510px;top:518px;width:180px;height:67px">Book Now</div>
<div class="dot" style="top:374px"></div>
<div class="dot" style="top:392px"></div>
<div class="dot on" style="top:410px"></div>
<div class="dot" style="top:428px"></div>
<div class="dot" style="top:446px"></div>
<svg class="abs" style="left:0;top:680px" width="1200" height="100" viewBox="0 0 1200 100">
  <defs><linearGradient id="heroBand" x1="0" x2="1"><stop offset="0.5" stop-color="#e8603c"/><stop offset="0.5" stop-color="#f0b84b"/></linearGradient></defs>
  <path d="M0 95 Q600 -71 1200 95 L1200 100 Q600 -32 0 100Z" fill="url(#heroBand)"/>
  <path d="M0 100 Q600 -32 1200 100Z" fill="#fff"/>
</svg>

<!-- about -->
<h2 class="abs about-title display">About<br>Marla Dunbevy</h2>
<p class="abs about-text">Marla has been traveling full time for the past two years and has been passionate about travel from a young age. Marla is dedicated to working closely with clients to book their dream vacation. Her specializations include honeymoons and anniversaries, focusing on travel in Europe, Hawaii and all inclusive resorts in the Caribbean. Every itinerary is planned with care, from the first call to the day you return home.</p>
<div class="btn" style="left:146px;top:1208px;width:181px;height:69px">Read More</div>
<svg class="abs" style="left:590px;top:824px" width="464" height="464" viewBox="0 0 464 464">
  <circle cx="232" cy="232" r="205" fill="none" stroke="#f0b84b" stroke-width="20" stroke-dasharray="900 388" transform="rotate(-60 232 232)"/>
  <circle cx="232" cy="232" r="205" fill="none" stroke="#e8603c" stroke-width="20" stroke-dasharray="180 1108" transform="rotate(150 232 232)"/>
  <circle cx="232" cy="232" r="205" fill="none" stroke="#e8603c" stroke-width="20" stroke-dasharray="40 1248" transform="rotate(-45 232 232)"/>
</svg>
<div class="abs portrait" role="img" aria-label="Portrait photo of agency owner Marla Dunbevy"></div>

<!-- specialties -->
<svg class="abs" style="left:0;top:1350px" width="1200" height="748" viewBox="0 0 1200 748">
  <path d="M0 87 Q600 -87 1200 87 L1200 660 Q600 836 0 660Z" fill="#e0dfe3"/>
</svg>
<h2 class="abs section-title display" style="top:1455px">We Specialize In</h2>
<div class="abs card card-hawaii" role="img" aria-label="Hawaiian beach at sunset under palm leaves">HAWAII</div>
<div class="abs card card-europe" role="img" aria-label="European landmarks under a blue sky">EUROPE</div>
<div class="abs card card-caribbean" role="img" aria-label="Aerial view of turquoise Caribbean water">CARIBBEAN</div>
<div class="btn" style="left:462px;top:1918px;width:277px;height:68px">View All Vacations</div>

<!-- gallery -->
<h2 class="abs section-title display" style="top:2202px">Photo Gallery</h2>
<div class="photo" style="left:98px;top:2315px;width:245px;height:163px;background:linear-gradient(180deg,#e6b07a,#3aa0a0)" role="img" aria-label="Venice waterfront at golden hour"></div>
<div class="photo" style="left:98px;top:2486px;width:245px;height:162px;background:linear-gradient(180deg,#6fb0d8,#1ab0b8 60%,#3a7a3a)" role="img" aria-label="Tropical island bay"></div>
<div class="photo" style="left:98px;top:2657px;width:245px;height:195px;background:linear-gradient(180deg,#d89060,#7a5a4a 55%,#2e2a2a)" role="img" aria-label="Old town bridge at dusk"></div>
<div class="photo" style="left:351px;top:2315px;width:245px;height:366px;background:linear-gradient(180deg,#4a2a7a,#c8305a 40%,#f0902a 65%,#1e3a1e)" role="img" aria-label="Vivid sunset over palms"></div>
<div class="photo" style="left:351px;top:2690px;width:245px;height:162px;background:linear-gradient(180deg,#0a1230,#1a3a6a)" role="img" aria-label="Earth at night from orbit"></div>
<div class="photo" style="left:605px;top:2315px;width:245px;height:163px;background:linear-gradient(180deg,#2a6ad0,#8ad0e8 60%,#e8f0f0)" role="img" aria-label="Woman on a white sand beach"></div>
<div class="photo" style="left:605px;top:2486px;width:245px;height:366px;background:linear-gradient(180deg,#5a7a5a,#4a9a3a 50%,#3a3a3a)" role="img" aria-label="Convertible drive through green mountains"></div>
<div class="photo" style="left:857px;top:2315px;width:245px;height:366px;background:linear-gradient(180deg,#e8a0b8,#f0902a 55%,#3a2a2a)" role="img" aria-label="Woman at infinity pool at sunset"></div>
<div class="photo" style="left:857px;top:2690px;width:245px;height:162px;background:linear-gradient(180deg,#6ac8e8,#18c8c8)" role="img" aria-label="Pier over turquoise water"></div>

<!-- footer -->
<svg class="abs" style="left:0;top:2900px" width="1200" height="120" viewBox="0 0 1200 120">
  <defs><linearGradient id="footBand" x1="0" x2="1"><stop offset="0.5" stop-color="#f0b84b"/><stop offset="0.5" stop-color="#e8603c"/></linearGradient></defs>
  <path d="M0 18 Q600 152 1200 18 L1200 22 Q600 198 0 22Z" fill="url(#footBand)"/>
  <path d="M0 22 Q600 198 1200 22 L1200 120 L0 120Z" fill="#1a1617"/>
</svg>
<div class="abs footer"></div>
<div class="abs footer-brand"><span class="mark"></span>Harbors &amp; Hammocks</div>

<div class="abs footer-head" style="left:183px">Get In Touch:</div>
<div class="field" style="left:185px;top:3257px;width:266px;height:28px">NAME :</div>
<div class="field" style="left:461px;top:3257px;width:266px;height:28px">PHONE :</div>
<div class="field" style="left:185px;top:3297px;width:542px;height:28px">EMAIL :</div>
<div class="field" style="left:185px;top:3337px;width:542px;height:66px">MESSAGE :</div>
<div class="btn submit">SUBMIT</div>

<div class="abs footer-head" style="left:782px">Contact Information</div>
<div class="abs contact-item" style="top:3233px">
  <span class="ring"><svg width="12" height="16" viewBox="0 0 12 16"><path d="M6 1a5 5 0 0 1 5 5c0 4-5 9-5 9S1 10 1 6a5 5 0 0 1 5-5z" fill="none" stroke="#fff" stroke-width="1.5"/><circle cx="6" cy="6" r="1.8" fill="#fff"/></svg></span>
  <span>121 Lorem ipsum dolor sit amet<br>consectetur adipiscin</span>
</div>
<div class="abs contact-item" style="top:3285px">
  <span class="ring"><svg width="14" height="14" viewBox="0 0 14 14"><path d="M3 1l2 3-1.5 1.5a8 8 0 0 0 5 5L10 9l3 2-1.5 2.5C6 13 1 8 .8 2.5z" fill="#fff"/></svg></span>
  <span>Phone : 1 800 555 0142</span>
</div>
<div class="abs contact-item" style="top:3330px">
  <span class="ring"><svg width="14" height="10" viewBox="0 0 14 10"><rect x="0.5" y="0.5" width="13" height="9" rx="1" fill="#fff"/><path d="M1 1l6 5 6-5" fill="none" stroke="#1a1617"/></svg></span>
  <span>marla@harborsandhammockstravel.example</span>
</div>

<div class="abs copyright">© 2021 Harbors and Hammocks Travel Agency. All rights reserved.Privacy Terms of Use</div>
<a class="abs social" style="left:927px" href="#" aria-label="Social link 1"></a>
<a class="abs social" style="left:966px" href="#" aria-label="Social link 2"></a>
<a class="abs social" style="left:1008px" href="#" aria-label="Social link 3"></a>

</body>
</html>
```